Geschäftspapiere für Personalvermittler
Sehr Guter Disigner. Versteht alles und setzt alles schnell um. Wir danken TREVO314 für die gute Zusammenarbeit. Velmuran UG
Zielgruppe
Das Startup ist ein Experte für die Personalvermittlung von Fachkräften und Führungskräften in verschiedenen Branchen.
Neben der Rekrutierung von Fach- und Führungskräften können wir auch Softwareentwicklungsdienste anbieten.
Hallo liebe Designer,
wir freuen uns, dass Sie sich für unseren Wettbewerb interessieren.
Wir benötigen ein design für
1) Visitenkarten + QR-Code
2) Briefpappier
Folgende Informationen müssen im Geschäftspapier vorhanden sein:
Firmenname
Adresse
Tel
Fax
Internet
E-Mail
Name Bank
IBAN
BIC
Geschäftsführer
Sitz der Gesellschaft: Hamburg
Amtsgericht
Wir setzen Eurer Phantasie keine Grenzen und brauchen innovative Ideen.
Bitte verwenden Sie ein QR-Code.
Wir wünschen viel Erfolg.
Ihr Velmuran Team

```html
<!DOCTYPE html>
<html lang="de">
<head>
<meta charset="utf-8">
<title>Velmuran – Geschäftspapiere</title>
<link href="https://fonts.googleapis.com/css2?family=Source+Sans+3:wght@400;600&display=swap" rel="stylesheet">
<style>
  :root {
    --orange: #f2990f;
    --blue: #2196d3;
    --grey-text: #7a7a7a;
    --paper: #ffffff;
    --faint: #f1f1ef;
    --shadow: 4px 4px 6px rgba(0,0,0,.45);
  }
  * { margin: 0; padding: 0; box-sizing: border-box; }
  html, body { width: 1200px; height: 1200px; overflow: hidden; background: #fff; }
  body { position: relative; font-family: "Source Sans 3", sans-serif; color: var(--grey-text); }

  .sheet { position: absolute; }

  /* Letterhead */
  .letterhead {
    left: 69px; top: 226px; width: 507px; height: 717px;
    background: var(--orange); box-shadow: var(--shadow);
  }
  .letterhead__page {
    position: absolute; left: 14px; top: 10px; right: 14px; bottom: 11px;
    background: var(--paper); overflow: hidden;
  }
  .brand-name {
    font-family: "Source Sans 3", sans-serif; font-weight: 600; color: var(--blue);
    letter-spacing: .04em; text-transform: uppercase; white-space: nowrap;
  }
  .brand-square { display: inline-block; background: var(--orange); vertical-align: middle; }
  .letterhead__brand {
    position: absolute; left: 37px; width: 400px; top: 60px; text-align: center; font-size: 26px;
  }
  .letterhead__brand .brand-square { width: 12px; height: 12px; margin-left: 8px; }
  .sender-line {
    position: absolute; left: 59px; top: 110px; font-size: 5.5px; white-space: nowrap;
  }
  .sender-line .brand-name { font-size: 5.5px; }
  .sender-line .dot { color: var(--orange); margin: 0 2px; }
  .letterhead__divider {
    position: absolute; left: 385px; top: 0; width: 1px; height: 127px; background: var(--orange);
  }
  .contact-column {
    position: absolute; left: 395px; top: 6px; width: 78px;
    font-size: 7px; line-height: 10.3px; white-space: nowrap; font-style: normal;
  }
  .contact-column .brand-name { font-size: 7px; }
  .contact-column .group { margin-top: 8px; }
  .contact-column .label { display: inline-block; width: 20px; }
  .letterhead__mark {
    position: absolute; left: 0; width: 480px; top: 350px; text-align: center;
    font-size: 64px; font-weight: 600; color: var(--faint); letter-spacing: .04em; text-transform: uppercase;
  }

  /* Envelope back */
  .envelope-back {
    left: 602px; top: 290px; width: 561px; height: 281px;
    background: var(--paper); box-shadow: var(--shadow);
  }
  .envelope-back__flap { position: absolute; left: 0; top: 0; width: 561px; height: 90px; overflow: visible; }
  .envelope-back__name {
    position: absolute; left: 0; width: 561px; top: 26px; text-align: center;
    font-size: 17px; font-weight: 600; color: #fff; letter-spacing: .04em; text-transform: uppercase;
  }

  /* Envelope front */
  .envelope-front {
    left: 602px; top: 661px; width: 561px; height: 282px;
    background: var(--orange); box-shadow: var(--shadow);
  }
  .envelope-front__face {
    position: absolute; left: 10px; top: 10px; right: 10px; bottom: 10px; background: var(--paper);
  }
  .return-address {
    position: absolute; left: 18px; top: 17px; font-size: 8px; line-height: 12.2px; font-style: normal;
  }
  .return-address .brand-name { font-size: 8px; }
  .envelope-front__brand {
    position: absolute; right: 28px; top: 205px; font-size: 25px;
  }
  .envelope-front__brand .brand-square { width: 12px; height: 12px; margin-left: 8px; }
  .gmbh { font-size: .6em; color: var(--grey-text); margin-left: 1px; }
</style>
</head>
<body>

<section class="sheet letterhead">
  <div class="letterhead__page">
    <div class="letterhead__brand"><span class="brand-name">Velmuran</span><span class="brand-square"></span></div>

    <p class="sender-line"><span class="brand-name">Velmuran</span><span class="gmbh">GMBH</span>
      <span class="dot">•</span>Falkenstieg 9 <span class="dot">•</span>31045 Ostenhagen <span class="dot">•</span>Germany</p>

    <div class="letterhead__divider"></div>

    <address class="contact-column">
      <div><span class="brand-name">Velmuran</span><span class="gmbh">GMBH</span></div>
      <div>Falkenstieg 9</div>
      <div>31045 Ostenhagen</div>
      <div>Germany</div>
      <div class="group">
        <div><span class="label">Telf.:</span> 0 41 52 / 6 28 14-0</div>
        <div><span class="label">Fax:</span> 0 41 52 / 6 28 14-0</div>
        <div><span class="label">Movil:</span> 000 514 226 3081</div>
      </div>
      <div class="group">
        <div>Mail- info@velmuran.de</div>
        <div>Web: www. velmuran.de</div>
      </div>
    </address>

    <div class="letterhead__mark" aria-hidden="true">Velmuran</div>
  </div>
</section>

<section class="sheet envelope-back">
  <svg class="envelope-back__flap" viewBox="0 0 561 90" aria-hidden="true">
    <defs>
      <filter id="flapShadow" x="-5%" y="-10%" width="110%" height="130%">
        <feDropShadow dx="3" dy="4" stdDeviation="3" flood-color="#000" flood-opacity=".45"/>
      </filter>
    </defs>
    <path d="M0 0 H561 L535 73 Q529 79 517 79 H44 Q32 79 26 73 Z" fill="#f2990f" filter="url(#flapShadow)"/>
  </svg>
  <div class="envelope-back__name">Velmuran</div>
</section>

<section class="sheet envelope-front">
  <div class="envelope-front__face">
    <address class="return-address">
      <div><span class="brand-name">Velmuran</span><span class="gmbh">GMBH</span></div>
      <div>Falkenstieg 9</div>
      <div>31045 Ostenhagen</div>
      <div>Germany</div>
    </address>
    <div class="envelope-front__brand"><span class="brand-name">Velmuran</span><span class="brand-square"></span></div>
  </div>
</section>

</body>
</html>
```